Web Developer Wordpress theme

I'm a web developer but a poor designer so i need somebody to design me a cool and professional WordPress theme. I specialize in shopping cart developments and modifications as well as hosting for these system so would like the design to show this off. I am UK based and want this to also come across in the design.
As for colors and layout i am open mined just use your imaginantion i will let know what i think of your designs.
also forgot to mention my business name is valtrique
and my exsiting site is valtrique.co.uk

```html
<!DOCTYPE html>
<html lang="en">
<head>
<meta charset="utf-8">
<title>Valtrique — serious web development</title>
<link rel="stylesheet" href="https://fonts.googleapis.com/css2?family=Roboto+Condensed:wght@300;400;700&family=Arimo:wght@400;700&display=swap">
<style>
:root{
  --blue:#0f6a97;
  --blue-dark:#0b5a82;
  --blue-line:#3f8fb8;
  --sky:#b6dcf1;
  --field:#9ec9df;
  --orange:#f39420;
  --grey-band:#e5e5e5;
  --grey-text:#6b6b6b;
  --btn-grey:#8f8f8f;
  --link:#1a8fc7;
  --white:#fff;
}
*{box-sizing:border-box;margin:0;padding:0}
html,body{width:1200px;height:1182px;overflow:hidden;background:var(--white)}
body{position:relative;font-family:"Arimo",Arial,sans-serif}
.abs{position:absolute}
.cond{font-family:"Roboto Condensed",Arial,sans-serif}

.brand{left:53px;top:0;width:330px;height:121px;background:var(--white);border:1px solid #e2e2e2;border-top:none;border-radius:0 0 8px 8px;box-shadow:0 4px 6px rgba(0,0,0,.12)}
.brand-name{position:absolute;left:22px;top:18px;font-family:"Roboto Condensed",sans-serif;font-weight:700;font-size:58px;color:var(--orange);letter-spacing:-1px;line-height:1}
.brand-mark{position:absolute;left:18px;top:28px;width:0}
.brand-tag{position:absolute;left:100px;top:85px;font-size:11px;letter-spacing:1.5px;color:#777;font-weight:700}

.social{left:985px;top:0;width:163px;height:55px;background:#eaeaea;border-radius:0 0 8px 8px}
.social span{position:absolute;top:8px;width:36px;height:36px;border-radius:50%}

.nav{left:482px;top:67px;width:666px;height:50px;background:var(--blue);border-radius:6px;box-shadow:inset 0 -3px 0 var(--blue-dark)}
.nav a{position:absolute;top:13px;transform:translateX(-50%);color:var(--white);text-decoration:none;font-family:"Roboto Condensed",sans-serif;font-size:21px}

.sidebar{left:53px;top:147px;width:332px;height:676px;background:var(--blue);border:3px solid #5aa0c6;border-radius:8px}
.search{left:76px;top:172px;width:285px;height:35px;background:var(--field);border-radius:7px;font-size:12px;color:#244;padding:10px 0 0 16px;letter-spacing:.5px}
.ad{width:135px;height:125px;background:#000;border:4px solid var(--white);text-align:center;font-family:"Roboto Condensed",sans-serif;font-weight:700;font-size:24px;line-height:25px;color:var(--white);padding-top:10px}
.ad em{font-style:normal;color:var(--orange)}
.ad i{display:block;margin:4px auto 0;width:20px;height:20px;border-radius:50%;background:var(--white);position:relative}
.ad i:after{content:"";position:absolute;left:5px;top:7px;border:5px solid transparent;border-top:7px solid #000}
.side-h{color:var(--white);font-family:"Roboto Condensed",sans-serif;font-weight:700;font-size:26px}
.side-rule{height:1px;background:var(--blue-line);width:285px;left:76px}
.side-links a{position:absolute;left:100px;color:var(--white);font-size:16px;text-decoration:none}
.side-links a:before{content:"";position:absolute;left:-22px;top:5px;width:9px;height:9px;border:2px solid var(--orange);border-left:none;border-bottom:none;transform:rotate(45deg)}
.hl{left:76px;top:534px;width:285px;height:24px;background:linear-gradient(90deg,var(--orange) 40%,rgba(243,148,32,0))}
.email{left:76px;top:720px;width:285px;height:35px;background:var(--field);border-radius:7px;font-size:12px;color:#244;padding:11px 0 0 16px}
.pill{height:29px;border-radius:15px;background:linear-gradient(#2b8dc4,#0d5d8a);color:var(--white);font-size:12px;padding:8px 0 0 16px;box-shadow:0 3px 4px rgba(0,0,0,.25)}
.pill b{position:absolute;right:10px;top:6px;width:17px;height:17px;border-radius:50%;background:var(--white)}
.pill b:after{content:"";position:absolute;left:6px;top:4px;border:4.5px solid transparent;border-left:6px solid #0d5d8a}

.post-title{left:418px;width:480px;font-family:"Roboto Condensed",sans-serif;font-weight:300;font-size:27px;line-height:32px;color:var(--orange)}
.post-body{left:419px;width:560px;font-size:12px;line-height:23.5px;color:#1474a8;letter-spacing:.6px}
.post-img{left:997px;width:151px;height:138px;border-radius:10px;border:4px solid #8a8a8a;background:linear-gradient(145deg,#e9f0f7,#5d8fc9 60%,#2a5f9e)}
.meta{left:417px;width:731px;height:44px;background:var(--sky);border-radius:6px}
.meta p{position:absolute;left:14px;top:16px;font-size:11px;color:var(--white);letter-spacing:.7px}
.meta p span{color:#0f6a97}
.btn{position:absolute;top:8px;height:30px;border-radius:4px;color:var(--white);font-family:"Roboto Condensed",sans-serif;font-size:17px;text-align:center;padding-top:5px}
.btn-dark{left:497px;width:114px;background:var(--blue)}
.btn-grey{left:620px;width:101px;background:var(--btn-grey)}

.band{left:0;top:891px;width:1200px;height:254px;background:var(--grey-band)}
.foot-h{top:902px;font-family:"Roboto Condensed",sans-serif;font-size:26px;color:var(--grey-text)}
.foot-rule{top:939px;height:1px;width:276px;background:#cfcfcf}
.fb-link{left:87px;font-size:12px;color:var(--link);letter-spacing:.6px}
.fb-text{left:87px;font-size:12px;line-height:25px;color:#444;letter-spacing:.6px}
.dots{left:85px;width:276px;border-top:1px dotted #bbb}
.field{left:462px;width:275px;background:#fafafa;border:1px solid #ddd;font-size:12px;color:#333;padding:9px 0 0 10px;letter-spacing:.8px}
.promo{left:851px;top:958px;width:255px;height:145px;border-radius:6px;background:linear-gradient(#4ba8dc,#1b79b4);box-shadow:0 8px 8px -4px rgba(0,0,0,.3);color:var(--white)}
.ribbon{left:838px;top:980px;width:110px;height:26px;background:#b3141c;transform:rotate(-45deg);color:var(--white);font-size:10px;text-align:center;padding-top:7px;letter-spacing:.5px}
.arrow{top:1111px;width:17px;height:17px;border-radius:50%;background:#888}
.arrow:after{content:"";position:absolute;top:4px;border:4.5px solid transparent}
.arrow.prev:after{left:1px;border-right:6px solid var(--white)}
.arrow.next:after{left:6px;border-left:6px solid var(--white)}
.copy{left:0;top:1145px;width:1200px;height:37px;background:#fafafa;text-align:center;font-size:11px;color:#888;padding-top:12px;letter-spacing:.8px}
</style>
</head>
<body>

<header>
  <div class="abs brand">
    <div class="brand-name">Valtrique</div>
    <div class="brand-tag">serious web developement</div>
  </div>
  <div class="abs social" aria-label="Social links">
    <span style="left:9px;background:#f29a24"></span>
    <span style="left:63px;background:#1b8ec8"></span>
    <span style="left:117px;background:#1f64a9"></span>
  </div>
  <nav class="abs nav">
    <a style="left:77px">Home</a>
    <a style="left:180px">About Us</a>
    <a style="left:293px">Services</a>
    <a style="left:399px">Addons</a>
    <a style="left:503px">Contact</a>
    <a style="left:593px">Blog</a>
  </nav>
</header>

<aside>
  <div class="abs sidebar"></div>
  <div class="abs search">Search here....
    <svg class="abs" style="right:10px;top:7px" width="24" height="22" viewBox="0 0 24 22"><circle cx="9" cy="9" r="6" fill="none" stroke="#fff" stroke-width="2.5"/><line x1="13.5" y1="13" x2="21" y2="19" stroke="#fff" stroke-width="3.5" stroke-linecap="round"/></svg>
  </div>
  <div class="abs ad" style="left:76px;top:221px">You can<br><em>Advertise</em><br>HERE<i></i></div>
  <div class="abs ad" style="left:225px;top:221px">You can<br><em>Advertise</em><br>HERE<i></i></div>
  <div class="abs ad" style="left:76px;top:357px">You can<br><em>Advertise</em><br>HERE<i></i></div>
  <div class="abs ad" style="left:225px;top:357px">You can<br><em>Advertise</em><br>HERE<i></i></div>

  <h3 class="abs side-h" style="left:75px;top:489px">Links Here</h3>
  <div class="abs side-rule" style="top:525px"></div>
  <div class="abs hl"></div>
  <div class="side-links">
    <a style="top:535px">Home</a>
    <a style="top:562px">About Us</a>
    <a style="top:589px">Services</a>
    <a style="top:616px">Addons</a>
    <a style="top:643px">Contact Us</a>
  </div>

  <h3 class="abs side-h" style="left:75px;top:672px">Subscribe</h3>
  <div class="abs side-rule" style="top:706px"></div>
  <div class="abs email">Enter email</div>
  <div class="abs pill" style="left:81px;top:769px;width:104px">Subscribe<b></b></div>
</aside>

<main>
  <article>
    <h2 class="abs post-title" style="top:156px">Lorem ipsum dolor sit amet, consectetur adipiscing elit. Mauris ut</h2>
    <p class="abs post-body" style="top:234px">Lorem Ipsum is simply dummy text of the printing and typesetting industry. Lorem Ipsum has been the industry's standard dummy text ever since the 1500s, when an unknown printer took a galley of type and scrambled it to make a type specimen book. It has survived</p>
    <div class="abs post-img" style="top:150px" role="img" aria-label="Blog post thumbnail"></div>
    <div class="abs meta" style="top:320px"><p>Posted by <span>Valtrique</span> on Jan 3, 2012</p><span class="btn btn-dark">0 comments</span><span class="btn btn-grey">Read more</span></div>
  </article>
  <article>
    <h2 class="abs post-title" style="top:403px">Lorem ipsum dolor sit amet, consectetur adipiscing elit. Mauris ut</h2>
    <p class="abs post-body" style="top:481px">Lorem Ipsum is simply dummy text of the printing and typesetting industry. Lorem Ipsum has been the industry's standard dummy text ever since the 1500s, when an unknown printer took a galley of type and scrambled it to make a type specimen book. It has survived</p>
    <div class="abs post-img" style="top:397px" role="img" aria-label="Blog post thumbnail"></div>
    <div class="abs meta" style="top:567px"><p>Posted by <span>Valtrique</span> on Jan 3, 2012</p><span class="btn btn-dark">0 comments</span><span class="btn btn-grey">Read more</span></div>
  </article>
  <article>
    <h2 class="abs post-title" style="top:650px">Lorem ipsum dolor sit amet, consectetur adipiscing elit. Mauris ut</h2>
    <p class="abs post-body" style="top:728px">Lorem Ipsum is simply dummy text of the printing and typesetting industry. Lorem Ipsum has been the industry's standard dummy text ever since the 1500s, when an unknown printer took a galley of type and scrambled it to make a type specimen book. It has survived</p>
    <div class="abs post-img" style="top:644px" role="img" aria-label="Blog post thumbnail"></div>
    <div class="abs meta" style="top:814px"><p>Posted by <span>Valtrique</span> on Jan 3, 2012</p><span class="btn btn-dark">0 comments</span><span class="btn btn-grey">Read more</span></div>
  </article>
</main>

<footer>
  <div class="abs band"></div>

  <h4 class="abs foot-h" style="left:85px">From Blog</h4>
  <div class="abs foot-rule" style="left:85px"></div>
  <p class="abs fb-link" style="top:951px">Quisque euismod orci...</p>
  <p class="abs fb-text" style="top:970px">Nulla luctus, purus in molestie posuere,<br>lorem...</p>
  <div class="abs dots" style="top:1025px"></div>
  <p class="abs fb-link" style="top:1038px">Quisque euismod orci...</p>
  <p class="abs fb-text" style="top:1057px">Nulla luctus, purus in molestie posuere,<br>lorem...</p>
  <div class="abs dots" style="top:1113px"></div>

  <h4 class="abs foot-h" style="left:462px">Quick Contact</h4>
  <div class="abs foot-rule" style="left:462px"></div>
  <div class="abs field" style="top:951px;height:31px">Name</div>
  <div class="abs field" style="top:987px;height:31px">Email</div>
  <div class="abs field" style="top:1023px;height:73px">Subject</div>
  <div class="abs pill" style="left:466px;top:1105px;width:104px;height:27px;padding-top:7px">SUBMIT<b style="top:5px"></b></div>

  <h4 class="abs foot-h" style="left:840px">Quickstart Package</h4>
  <div class="abs foot-rule" style="left:840px"></div>
  <div class="abs promo">
    <div class="abs cond" style="left:64px;top:34px;font-size:20px;font-weight:700;color:#e8f4fb">Shopping Cart Hosting</div>
    <div class="abs" style="left:64px;top:62px;font-size:12px;line-height:20px;letter-spacing:.3px">Lorem ipsum dolor sit amet,<br>consectetuer adipiscing elit,</div>
    <div class="abs" style="left:64px;top:111px;font-size:12px;text-decoration:underline">Learn more</div>
  </div>
  <div class="abs ribbon">ORDER NOW</div>
  <span class="abs arrow prev" style="left:1057px"></span>
  <span class="abs arrow next" style="left:1082px"></span>

  <div class="abs copy">Website content Copyrighted Valtrique 2012</div>
</footer>

</body>
</html>
```